"Vine Hollow Excursions" is a top notch Santa Barbara County Wine Tour company.

We provide scenic, boutique and custom wine tours. I need the card to be clean and classy. I will provide our logo. I would like the logo to cover the back side of the card as an option and would like to see a couple color options other then our signature green and gold. I would like to see some creative options and let the designers come up with options.
I need cards for myself and my team. The final design should communicate "An authentic and boutique wine tour experience"
Please use my website for reference www.vinehollowexcursions.example

Target Market(s)

We have a wide range of clients from millennials to baby boomers

Industry/Entity Type

Tour

Contact Information for Business Card

Contact info:
Dale Morton
805-219-6384
info@vinehollowexcursions.example
vinehollowexcursions.example

Colors

Designer to choose colors to be used in the design.

Requirements
Must have
• my logo
Nice to have
• *I would like to have the backside side with the logo and the company statement
• "An authentic and boutique wine tour experience" as an option.
• *I would also like to see what the designers can create!
• *I would like to see an option that incorporates or social: instagram, yelp, Tour Advisor
Should not have
• I do not want it too busy.

```html
<!DOCTYPE html>
<html lang="en">
<head>
<meta charset="utf-8">
<title>Vine Hollow Excursions – Business Card</title>
<link href="https://fonts.googleapis.com/css2?family=Montserrat:wght@400;500;600&display=swap" rel="stylesheet">
<style>
  :root {
    --backdrop: #2b2b2b;
    --card: #1d1d1d;
    --green: #26674a;
    --gold: #b59871;
    --ink: #f1efea;
  }
  * { margin: 0; padding: 0; box-sizing: border-box; }
  html, body { width: 1200px; height: 900px; overflow: hidden; }
  body {
    background: var(--backdrop);
    font-family: "Montserrat", sans-serif;
    position: relative;
  }
  .card {
    position: absolute;
    left: 250px;
    width: 700px;
    height: 400px;
    background: var(--card);
    box-shadow: 0 10px 30px rgba(0,0,0,.45);
    overflow: hidden;
  }
  .card--front { top: 40px; }
  .card--back { top: 460px; }

  .brand {
    position: absolute;
    inset: 0;
    display: flex;
    align-items: center;
    justify-content: center;
    gap: 14px;
  }
  .brand__dot {
    width: 22px; height: 22px;
    border-radius: 50%;
    background: var(--green);
  }
  .brand__name {
    font-weight: 500;
    font-size: 30px;
    letter-spacing: 3px;
    text-transform: uppercase;
    color: var(--gold);
  }

  .identity {
    position: absolute;
    right: 430px;
    top: 130px;
    text-align: right;
  }
  .identity__name {
    font-weight: 500;
    font-size: 36px;
    letter-spacing: 2px;
    color: var(--green);
    text-transform: uppercase;
    line-height: 1.1;
  }
  .identity__title {
    font-weight: 600;
    font-size: 22px;
    letter-spacing: 1px;
    color: var(--gold);
    text-transform: uppercase;
  }
  .divider {
    position: absolute;
    left: 290px;
    top: 125px;
    width: 2px;
    height: 120px;
    background: var(--gold);
  }
  .contact {
    position: absolute;
    left: 312px;
    top: 130px;
    list-style: none;
    font-size: 15px;
    color: var(--ink);
    line-height: 23px;
  }
  .contact li { display: flex; align-items: center; gap: 8px; white-space: nowrap; }
  .contact .accent { color: var(--gold); }
  .contact__icon { width: 11px; height: 11px; flex: none; }
  .contact__pair { display: flex; gap: 14px; }
  .contact__pair span { display: flex; align-items: center; gap: 8px; }
  .social-dot {
    width: 10px; height: 10px;
    border-radius: 50%;
    background: var(--ink);
    flex: none;
  }
  .wave { position: absolute; left: 0; bottom: 0; width: 700px; height: 130px; }
</style>
</head>
<body>

<section class="card card--front">
  <div class="brand">
    <span class="brand__dot"></span>
    <span class="brand__name">Vine Hollow Excursions</span>
  </div>
</section>

<section class="card card--back">
  <div class="identity">
    <h1 class="identity__name">Dale Morton</h1>
    <p class="identity__title">Tour Advisor</p>
  </div>
  <div class="divider"></div>
  <ul class="contact">
    <li>
      <svg class="contact__icon" viewBox="0 0 12 12"><path d="M3 1l2 2-1 1.5c.7 1.5 1.8 2.6 3.5 3.5L9 7l2 2-1.5 2C5 10.5 1.5 7 1 2.5z" fill="var(--gold)"/></svg>
      805-219-6384
    </li>
    <li>
      <svg class="contact__icon" viewBox="0 0 12 12"><rect x="1" y="2.5" width="10" height="7" fill="none" stroke="var(--gold)" stroke-width="1"/><path d="M1 2.5l5 4 5-4" fill="none" stroke="var(--gold)" stroke-width="1"/></svg>
      info@vinehollowexcursions.example
    </li>
    <li>
      <svg class="contact__icon" viewBox="0 0 12 12"><circle cx="6" cy="6" r="5" fill="none" stroke="var(--gold)"/><ellipse cx="6" cy="6" rx="2.2" ry="5" fill="none" stroke="var(--gold)"/><path d="M1 6h10" stroke="var(--gold)"/></svg>
      <span>www.<span class="accent">vinehollowexcursions</span>.example</span>
    </li>
    <li class="contact__pair">
      <span><i class="social-dot"></i>/vinehollowexcursions</span>
      <span><i class="social-dot"></i>@vinehollowexcursions</span>
    </li>
    <li class="contact__pair">
      <span><i class="social-dot"></i>biz/vinehollowexcursions</span>
      <span><i class="social-dot"></i>@sbcvinehollow</span>
    </li>
  </ul>
  <svg class="wave" viewBox="0 0 700 130" preserveAspectRatio="none">
    <path d="M0 40 C120 10 260 20 380 75 C470 115 580 125 700 118 L700 130 L0 130 Z" fill="var(--green)"/>
    <path d="M0 33 C120 3 260 13 380 68 C470 108 580 118 700 111" fill="none" stroke="var(--card)" stroke-width="6"/>
    <path d="M0 30 C120 0 260 10 380 65 C470 105 580 115 700 108" fill="none" stroke="var(--gold)" stroke-width="4"/>
  </svg>
</section>

</body>
</html>
```